Mortgage and Asset Finance Broker Needs a Wordpress Website Design

I need a modern looking Wordpress website to showcase my service as a mortgage and asset broker. I have a company and we work with various lenders to arrange mortgages, as well as commercial lending and business asset finance. The website needs to look professional, be easy to navigate and capture leads. SEO is obviously very important to me. It really needs to be something that shows trust and professioanlism.
Updates

On the home page I will need to have some boxes for Home Loans, Refinancing, Business (and Agriculture) Loans etc. I'd like a carousel in the middle which shows our lenders (so that can have the banks logos added).

It needs to be easy top navigate and showcase all we do - Home Loans, Refinancing, Commercial Loans, Car Loans, Asset Finance etc.

There are plenty of companies on the internet that do this.

There is some good information here https://lendplatehq.com.au/mortgage-broker-homepage/

I need to make sure that editing the website is easy (I think Wordpress has something that allows that).

Also we are very much an Australian business so that is something to advertise.

Industry/Entity Type

Mortgage and Finance Broker

Coding

Coded - Design and coding required

Number of Pages Required

5+ page

Requirements
Must have
• Easy to navigate professional feel. Must be responsive and mobile friendly.
Nice to have
• Homepage with links to inner pages. Contact buttons.

```html
<!DOCTYPE html>
<html lang="en">
<head>
<meta charset="utf-8">
<title>Northvale Financial Services – Home</title>
<link href="https://fonts.googleapis.com/css2?family=Outfit:wght@400;500;600;700&family=Montserrat:wght@400;500;600;700&display=swap" rel="stylesheet">
<style>
:root{
  --purple:#5e2a84;
  --orange:#f07f1e;
  --blue:#0d4a9b;
  --navy:#0f3f8a;
  --pink:#e01f5a;
  --ink:#1d1d2b;
  --text:#3b3b48;
  --cream:#fdf6ef;
  --line:#e6e6ee;
  --white:#fff;
}
*{box-sizing:border-box;margin:0;padding:0}
html,body{width:1200px;height:4370px;overflow:hidden}
body{font-family:"Montserrat",sans-serif;color:var(--text);background:var(--white);position:relative}
h1,h2,h3{font-family:"Outfit",sans-serif;color:var(--ink)}
.abs{position:absolute}
.btn{position:absolute;display:flex;align-items:center;justify-content:center;border-radius:30px;font-weight:700;font-size:14px;letter-spacing:.3px;text-transform:uppercase}
.btn-orange{background:var(--orange);color:#fff}
.btn-soft{background:#fdeee0;color:var(--orange)}
.btn-blue{background:var(--blue);color:#fff}
.section-title{position:absolute;left:0;width:1200px;text-align:center;font-size:47px;font-weight:500}
.underline{position:absolute;height:4px;width:76px;background:var(--orange);border-radius:2px}

/* top bar */
.topbar{position:absolute;top:0;left:0;width:1200px;height:46px;background:var(--purple);color:#fff;font-size:13px}
.topbar .email{left:112px;top:14px}
.topbar .call{left:707px;top:14px}
.social{position:absolute;top:0;width:36px;height:46px;border-left:1px solid rgba(255,255,255,.25)}
.social.active{background:var(--orange)}
.social i{position:absolute;left:13px;top:18px;width:10px;height:10px;border-radius:50%;background:#fff}

/* hero */
.hero{position:absolute;top:46px;left:0;width:1200px;height:554px;background:linear-gradient(90deg,#f6f1fa 0%,#f2ecf7 55%,#eadff0 100%)}
.hero-photo{position:absolute;right:0;top:80px;width:560px;height:474px;background:radial-gradient(ellipse at 60% 50%,#d9c2b0 0%,#cdb9d6 55%,#e8e0f0 100%)}
.brand{position:absolute;left:112px;top:22px;display:flex;align-items:center;gap:10px}
.brand-mark{width:22px;height:22px;background:var(--orange);border-radius:50%}
.brand-name{font-family:"Outfit",sans-serif;font-weight:700;font-size:22px;color:var(--blue);line-height:1.05}
.nav{position:absolute;top:45px;left:466px;display:flex;gap:30px;font-size:15px;font-weight:600;color:var(--ink)}
.nav .current{color:var(--blue);border-bottom:2px solid var(--blue);padding-bottom:3px}
.contact-btn{left:934px;top:32px;width:154px;height:46px;border:1px solid #f7c9a0;background:#fbe9dc;color:var(--orange);font-size:14px}
.hero h1{position:absolute;left:110px;top:180px;font-size:38px;font-weight:600;line-height:47px}
.hero h1 span{color:var(--blue)}
.hero p{position:absolute;left:112px;top:290px;width:480px;font-size:18px;line-height:28px;color:var(--ink)}
.hero .btn{left:112px;top:388px;width:154px;height:48px}

/* services */
.card{position:absolute;top:794px;width:307px;height:445px;background:#fff;border-radius:18px;box-shadow:0 6px 24px rgba(30,30,60,.12);text-align:center}
.card .icon{position:absolute;left:107px;top:38px;width:93px;height:93px;border-radius:50%}
.card .icon svg{position:absolute;left:26px;top:26px}
.card h3{position:absolute;top:155px;width:100%;font-family:"Montserrat",sans-serif;font-size:17px;font-weight:700;color:var(--blue)}
.card p{position:absolute;left:22px;top:188px;width:263px;font-size:15px;line-height:25px}
.card .btn{left:80px;top:366px;width:148px;height:46px}
.arrow{position:absolute;width:36px;height:36px;border-radius:50%}
.arrow.left{background:#e3ebf6}
.arrow.right{background:var(--orange)}
.arrow svg{position:absolute;left:12px;top:11px}

/* about */
.about{position:absolute;top:1320px;left:0;width:1200px;height:515px;background:linear-gradient(90deg,#0c3f86,#0e4b9d)}
.about-photo{position:absolute;left:112px;top:82px;width:428px;height:351px;background:linear-gradient(135deg,#9d9aa0 0%,#7d6f69 45%,#2d5a9c 100%)}
.about h2{position:absolute;left:592px;top:62px;font-size:50px;font-weight:500;color:#fff}
.about .underline{left:592px;top:116px}
.about p{position:absolute;left:592px;width:498px;font-size:15px;line-height:25px;color:#fff;text-align:justify}
.about .btn{left:592px;top:422px;width:150px;height:46px}

/* features */
.features h2{position:absolute;left:112px;top:1972px;font-size:50px;font-weight:500}
.features .underline{left:112px;top:2032px}
.features p{position:absolute;left:112px;width:425px;font-size:15px;line-height:25px}
.features .btn{left:112px;top:2337px;width:150px;height:48px}
.feat-photo-a{position:absolute;left:745px;top:1950px;width:343px;height:387px;background:linear-gradient(160deg,#0e2746 0%,#1f4f7f 55%,#0c1f38 100%)}
.feat-photo-b{position:absolute;left:604px;top:2120px;width:283px;height:296px;border:4px solid #fff;background:linear-gradient(135deg,#c7b8a6 0%,#6a5f5a 50%,#23222a 100%)}
.dots{position:absolute;left:895px;top:2345px;width:135px;height:40px;background-image:radial-gradient(#c9c9d6 2px,transparent 2.5px);background-size:12px 12px}

/* testimonials */
.clients{position:absolute;top:2520px;left:0;width:1200px;height:603px;background:var(--cream)}
.tcard{position:absolute;top:182px;width:305px;height:339px;background:#fff;border-radius:6px;box-shadow:0 4px 18px rgba(30,30,60,.08);text-align:center}
.tcard .q{position:absolute;left:128px;top:34px;width:50px;height:50px;border-radius:50%;background:var(--pink)}
.tcard .q svg{position:absolute;left:14px;top:15px}
.tcard p{position:absolute;left:20px;top:106px;width:265px;font-size:15px;line-height:25px;color:var(--ink)}
.tcard hr{position:absolute;left:22px;top:260px;width:261px;border:0;border-top:1px solid var(--line)}
.tcard h4{position:absolute;top:275px;width:100%;font-size:17px;font-weight:700;color:var(--blue)}
.tcard .stars{position:absolute;top:300px;width:100%;font-size:11px;letter-spacing:1px;color:var(--orange)}

/* lenders */
.lender{position:absolute;top:3318px;width:180px;height:90px;background:#fff;box-shadow:0 4px 18px rgba(30,30,60,.1);border-radius:4px}
.lender i{position:absolute;left:58px;top:27px;width:64px;height:36px;border-radius:6px;background:#e4e9f2}
.pager{position:absolute;top:3458px;width:11px;height:11px;border-radius:50%;background:#c9d3e3}
.pager.on{background:var(--orange)}

/* cta */
.cta-photo{position:absolute;left:0;top:3554px;width:600px;height:471px;background:linear-gradient(135deg,#d8d2cc 0%,#b09482 50%,#6e5a4f 100%)}
.cta{position:absolute;left:600px;top:3554px;width:600px;height:471px;background:var(--orange)}
.cta h2{position:absolute;left:62px;top:60px;font-size:47px;line-height:48px;font-weight:600;color:#fff}
.cta .underline{left:62px;top:168px;background:#fff}
.cta p{position:absolute;left:62px;top:200px;width:430px;font-size:15px;line-height:25px;color:#fff}
.cta .btn{left:62px;top:356px;width:158px;height:46px;font-size:14px}

/* footer */
.footer-brand{position:absolute;left:112px;top:4180px;display:flex;align-items:center;gap:12px}
.footer-brand .brand-name{font-size:28px}
.fcol h5{position:absolute;font-size:17px;font-weight:700;color:var(--purple)}
.fcol ul{position:absolute;list-style:none;font-size:14px;color:var(--ink)}
.fcol li{height:39px;padding-left:26px;position:relative}
.fcol li::before{content:"";position:absolute;left:0;top:6px;width:6px;height:6px;border-radius:50%;background:var(--navy)}
.ci{position:absolute;left:788px;width:36px;height:36px;border-radius:50%;background:#eef0f8}
.ci svg{position:absolute;left:11px;top:11px}
.ctext{position:absolute;left:847px;font-size:14px;line-height:21px;color:var(--ink)}
.footer-line{position:absolute;left:112px;top:4307px;width:976px;border-top:1px solid var(--line)}
.copy{position:absolute;left:412px;top:4332px;font-size:12px;font-weight:500;color:var(--ink)}
.fs{position:absolute;top:4321px;width:36px;height:36px;border-radius:50%;background:#eef0f8}
.fs.on{background:var(--orange)}
.fs i{position:absolute;left:13px;top:13px;width:10px;height:10px;border-radius:50%;background:var(--navy)}
.fs.on i{background:#fff}
</style>
</head>
<body>

<header class="topbar">
  <span class="abs email">✉&nbsp; Email Us: info@northvalefinance.example</span>
  <span class="abs call">☏&nbsp; Call Us: +1 (555) 014 2290</span>
  <a class="social active" style="left:938px" aria-label="Social profile 1"><i></i></a>
  <a class="social" style="left:976px" aria-label="Social profile 2"><i></i></a>
  <a class="social" style="left:1014px" aria-label="Social profile 3"><i></i></a>
  <a class="social" style="left:1052px;border-right:1px solid rgba(255,255,255,.25)" aria-label="Social profile 4"><i></i></a>
</header>

<section class="hero">
  <div class="hero-photo" role="img" aria-label="Smiling family of four at home"></div>
  <div class="brand">
    <span class="brand-mark"></span>
    <span class="brand-name">Northvale<br>Financial Services</span>
  </div>
  <nav class="nav">
    <a class="current">Home</a><a>About Us</a><a>Our Services</a><a>Reviews</a><a>Blog</a>
  </nav>
  <a class="btn contact-btn">Contact Us</a>
  <h1>Empowering Your<br><span>Home Ownership Journey</span></h1>
  <p>Lorem ipsum dolor sit amet, consectetur adipiscing elit, sed do eiusmod tempor incididunt ut labore et dolore magna aliqua.</p>
  <a class="btn btn-orange">Get Started</a>
</section>

<section class="services">
  <h2 class="section-title" style="top:688px">Our Services</h2>
  <span class="underline" style="left:562px;top:748px"></span>
  <a class="arrow left" style="left:43px;top:998px" aria-label="Previous"><svg width="12" height="14"><path d="M8 2 3 7l5 5" stroke="#0d4a9b" stroke-width="2" fill="none"/></svg></a>
  <a class="arrow right" style="left:1121px;top:998px" aria-label="Next"><svg width="12" height="14"><path d="M4 2l5 5-5 5" stroke="#fff" stroke-width="2" fill="none"/></svg></a>

  <article class="card" style="left:112px">
    <div class="icon" style="background:var(--blue)"><svg width="41" height="41"><path d="M4 20 20 6l17 14M9 17v18h22V17" stroke="#fff" stroke-width="3" fill="none"/><text x="16" y="30" fill="#fff" font-size="12" font-weight="700">%</text></svg></div>
    <h3>HOME LOANS</h3>
    <p>Lorem ipsum dolor sit amet, consectetur adipiscing elit, sed do eiusmod tempor incididunt ut labore et dolore magna aliqua. Ut enim ad minim veniam, quis nostrud exercita.</p>
    <a class="btn btn-soft">Learn More</a>
  </article>
  <article class="card" style="left:446px">
    <div class="icon" style="background:var(--pink)"><svg width="41" height="41"><path d="M3 22 15 12l12 10M7 20v15h16V20" stroke="#fff" stroke-width="3" fill="none"/><circle cx="32" cy="14" r="7" stroke="#fff" stroke-width="2.5" fill="none"/><text x="29" y="18" fill="#fff" font-size="10" font-weight="700">$</text></svg></div>
    <h3>REFINANCING LOANS</h3>
    <p>Lorem ipsum dolor sit amet, consectetur adipiscing elit, sed do eiusmod tempor incididunt ut labore et dolore magna aliqua. Ut enim ad minim veniam, quis nostrud exercita.</p>
    <a class="btn btn-orange">Learn More</a>
  </article>
  <article class="card" style="left:780px">
    <div class="icon" style="background:var(--purple)"><svg width="41" height="41"><rect x="3" y="12" width="26" height="16" rx="3" stroke="#fff" stroke-width="3" fill="none"/><circle cx="32" cy="12" r="7" stroke="#fff" stroke-width="2.5" fill="none"/><path d="M3 33h30" stroke="#fff" stroke-width="3"/></svg></div>
    <h3>COMMERCIAL LOANS</h3>
    <p>Lorem ipsum dolor sit amet, consectetur adipiscing elit, sed do eiusmod tempor incididunt ut labore et dolore magna aliqua. Ut enim ad minim veniam, quis nostrud exercita.</p>
    <a class="btn btn-soft">Learn More</a>
  </article>
</section>

<section class="about">
  <div class="about-photo" role="img" aria-label="Family smiling together at home"></div>
  <h2>About Us</h2>
  <span class="underline"></span>
  <p style="top:150px">Lorem ipsum dolor sit amet, consectetur adipiscing elit, sed do eiusmod tempor incididunt ut labore et dolore magna aliqua. Ut enim ad minim veniam, quis nostrud exercitation ullamco laboris nisi ut aliquip ex ea commodo consequat. Duis aute irure dolor in reprehenderit in voluptatea.</p>
  <p style="top:292px">Avelit esse cillum dolore eu fugiat nulla pariatur. Excepteur sint occaecat cupidatat non proident, sunt in culpa qui officia deserunt id est laborum.</p>
  <a class="btn btn-orange">Learn More</a>
</section>

<section class="features">
  <h2>Our Features</h2>
  <span class="underline"></span>
  <p style="top:2068px">Lorem ipsum dolor sit amet, consectetur adipiscing elit, sed do eiusmod tempor incididunt ut labore et dolore magna aliqua. Ut enim ad minim veniam, quis nostrud exercitation ullamco laboris nisi ut aliquip ex ea commo consequat. Duis aute irure dolor in reprehenderit in vullo laboris nisi ut aliquip oluptatea.</p>
  <p style="top:2231px">Avelit esse cillum dolore eu fugiat nulla pariatur cepteu sint occaecat cupidatat non proident, sunt in culpa qui officia deserunt id est laborum.</p>
  <a class="btn btn-orange">Learn More</a>
  <div class="feat-photo-a" role="img" aria-label="Hand pointing at a glowing house and percent symbol"></div>
  <div class="dots"></div>
  <div class="feat-photo-b" role="img" aria-label="Advisors meeting with clients at a table"></div>
</section>

<section class="clients">
  <h2 class="section-title" style="top:82px">What Our Clients Say</h2>
  <span class="underline" style="left:562px;top:140px"></span>
  <a class="arrow left" style="left:43px;top:352px" aria-label="Previous"><svg width="12" height="14"><path d="M8 2 3 7l5 5" stroke="#0d4a9b" stroke-width="2" fill="none"/></svg></a>
  <a class="arrow right" style="left:1121px;top:352px" aria-label="Next"><svg width="12" height="14"><path d="M4 2l5 5-5 5" stroke="#fff" stroke-width="2" fill="none"/></svg></a>
  <article class="tcard" style="left:112px">
    <span class="q"><svg width="22" height="20"><path d="M2 18V10l5-8h3L7 9h3v9zM12 18V10l5-8h3l-3 7h3v9z" fill="#fff"/></svg></span>
    <p>Lorem ipsum dolor sit amet, cons ectetur adipiscing elit, sed do eiusmod tempor incididunt ut labore et dolore magna aliqua. Ut enim ad minim veniam, quis nostrud ullamcoea.</p>
    <hr><h4>JOHN SMITH</h4><div class="stars">★★★★★</div>
  </article>
  <article class="tcard" style="left:447px">
    <span class="q"><svg width="22" height="20"><path d="M2 18V10l5-8h3L7 9h3v9zM12 18V10l5-8h3l-3 7h3v9z" fill="#fff"/></svg></span>
    <p>Lorem ipsum dolor sit amet, cons ectetur adipiscing elit, sed do eiusmod tempor incididunt ut labore et dolore magna aliqua. Ut enim ad minim veniam, quis nostrud ullamcoea.</p>
    <hr><h4>JOHN SMITH</h4><div class="stars">★★★★★</div>
  </article>
  <article class="tcard" style="left:783px">
    <span class="q"><svg width="22" height="20"><path d="M2 18V10l5-8h3L7 9h3v9zM12 18V10l5-8h3l-3 7h3v9z" fill="#fff"/></svg></span>
    <p>Lorem ipsum dolor sit amet, cons ectetur adipiscing elit, sed do eiusmod tempor incididunt ut labore et dolore magna aliqua. Ut enim ad minim veniam, quis nostrud ullamcoea.</p>
    <hr><h4>JOHN SMITH</h4><div class="stars">★★★★★</div>
  </article>
</section>

<section class="lenders">
  <h2 class="section-title" style="top:3210px">Our Lenders</h2>
  <span class="underline" style="left:562px;top:3268px"></span>
  <div class="lender" style="left:112px" aria-label="Lender badge"><i></i></div>
  <div class="lender" style="left:311px" aria-label="Lender badge"><i></i></div>
  <div class="lender" style="left:510px" aria-label="Lender badge"><i></i></div>
  <div class="lender" style="left:709px" aria-label="Lender badge"><i></i></div>
  <div class="lender" style="left:908px" aria-label="Lender badge"><i></i></div>
  <span class="pager" style="left:559px"></span>
  <span class="pager on" style="left:582px"></span>
  <span class="pager" style="left:605px"></span>
  <span class="pager" style="left:628px"></span>
</section>

<div class="cta-photo" role="img" aria-label="Family sitting on the floor under a cardboard roof"></div>
<section class="cta">
  <h2>Get Ready To<br>Start?</h2>
  <span class="underline"></span>
  <p>Lorem ipsum dolor sit amet, consectetur adipiscing elit, sed do eiusmod tempor incididunt ut labore et dolore magna aliqua. Ut enim ad minim veniam, quis nostrud exercitation ullamco laboris nisi ut aliquip ex ea commo conse duis aute irure dolorea.</p>
  <a class="btn btn-blue">Get Started</a>
</section>

<footer>
  <div class="footer-brand">
    <span class="brand-mark" style="width:26px;height:26px"></span>
    <span class="brand-name">Northvale<br>Financial Services</span>
  </div>
  <div class="fcol">
    <h5 style="left:391px;top:4098px">NAVIGATION</h5>
    <ul style="left:394px;top:4142px"><li>Home</li><li>About Us</li><li>Our Services</li><li>Reviews</li></ul>
    <h5 style="left:569px;top:4098px">QUICK LINKS</h5>
    <ul style="left:571px;top:4142px"><li>Contact Us</li><li>Blog</li><li>Privacy Policy</li><li>Terms&nbsp; Of Conditions</li></ul>
    <h5 style="left:788px;top:4098px">CONTACT US</h5>
  </div>
  <span class="ci" style="top:4130px"><svg width="14" height="14"><path d="M7 1a4.5 4.5 0 0 0-4.5 4.5C2.5 9 7 13 7 13s4.5-4 4.5-7.5A4.5 4.5 0 0 0 7 1z" fill="#0d4a9b"/><circle cx="7" cy="5.5" r="1.6" fill="#fff"/></svg></span>
  <span class="ctext" style="top:4130px">465, Lorum ipsum Dolore Sed Amet,<br>United States</span>
  <span class="ci" style="top:4190px"><svg width="14" height="14"><rect x="1" y="3" width="12" height="9" rx="1" fill="#0d4a9b"/><path d="M1 4l6 4 6-4" stroke="#fff" fill="none"/></svg></span>
  <span class="ctext" style="top:4198px">info@northvalefinance.example</span>
  <span class="ci" style="top:4248px"><svg width="14" height="14"><path d="M3 1h3l1 3-2 1.5a8 8 0 0 0 3.5 3.5L10 7l3 1v3a2 2 0 0 1-2 2A10 10 0 0 1 1 3a2 2 0 0 1 2-2z" fill="#0d4a9b"/></svg></span>
  <span class="ctext" style="top:4256px">+1 (555) 014 2290</span>
  <div class="footer-line"></div>
  <p class="copy">2025 © ALL RIGHTS RESERVED - NORTHVALE FINANCIAL SERVICES</p>
  <a class="fs on" style="left:922px" aria-label="Social profile 1"><i></i></a>
  <a class="fs" style="left:965px" aria-label="Social profile 2"><i></i></a>
  <a class="fs" style="left:1008px" aria-label="Social profile 3"><i></i></a>
  <a class="fs" style="left:1051px" aria-label="Social profile 4"><i></i></a>
</footer>

</body>
</html>
```